Kelvor Engineers: Why you should hire us keepsake

New design. Open to plastic cards. We are an engineering firm that designs cell phone towers and commercial buildings. Please check out our website www.kelvorstruct.com for more details. We want people to remember our card and for it to be useful if possible. We want the same look and feel on these cards to be translated to other marketing material we may need such as brochures.

Target Market(s)

Architects, Developers and Telecommunication Carriers

Industry/Entity Type

Engineering

Contact Information for Business Card

Card with our company colors, logo, and innovative design with elements related to our industry.

Font styles to use
Sans Serif

Colors
9bcb3c
abd036
0255a3

Requirements
Must have
• Sleek and hip design
Nice to have
• Bright lime green and navy coloring that pops with an innovative design.
Should not have
• A basic and boring design

```html
<!DOCTYPE html>
<html lang="en">
<head>
<meta charset="utf-8">
<title>Kelvor Engineers – Business Card</title>
<link rel="stylesheet" href="https://fonts.googleapis.com/css2?family=Roboto:wght@400;500;700&family=Roboto+Condensed:wght@700&display=swap">
<style>
  :root{
    --bg:#e9e9e7;
    --card-dark:#1d1e20;
    --card-light:#f4f4f3;
    --lime:#1fe61b;
    --navy:#0b2d5b;
    --text-light:#f2f2f2;
    --text-grey:#555a5e;
    --rule:#9a9a9a;
  }
  *{margin:0;padding:0;box-sizing:border-box}
  html,body{width:1200px;height:960px;overflow:hidden;background:var(--bg)}
  body{position:relative;font-family:"Roboto",Arial,sans-serif}

  .card{position:absolute;left:320px;width:600px;border-radius:18px;overflow:hidden}
  .card--front{top:108px;height:346px;background:var(--card-dark)}
  .card--back{top:493px;height:342px;background:var(--card-light)}

  .wordmark{position:absolute;color:var(--lime);font-family:"Roboto",Arial,sans-serif;font-weight:700;white-space:nowrap;letter-spacing:-0.5px}
  .card--front .wordmark{left:0;right:0;top:118px;text-align:center;font-size:58px;line-height:1}
  .card--back .wordmark{right:42px;top:52px;font-size:38px;line-height:1}

  .tagline{position:absolute;left:0;right:0;top:265px;display:flex;align-items:center;justify-content:center;gap:5px;
    color:var(--text-light);font-weight:700;font-size:15.5px;letter-spacing:0.3px;white-space:nowrap}
  .tagline::before,.tagline::after{content:"";width:28px;height:1.5px;background:var(--text-light)}
  .locations{position:absolute;left:0;right:0;top:288px;text-align:center;color:var(--text-light);font-size:15px;letter-spacing:0.8px;white-space:nowrap}

  .person{position:absolute;left:31px;top:180px;font-family:"Roboto Condensed","Arial Narrow",sans-serif;font-weight:700;font-size:21px;color:var(--lime);letter-spacing:0.2px}
  .rule{position:absolute;left:31px;right:40px;top:212px;height:1px;background:var(--rule)}
  .contacts{position:absolute;left:33px;top:226px;list-style:none}
  .contacts li{display:flex;align-items:center;gap:8px;height:19px;font-size:14.5px;color:var(--text-grey)}
  .contacts svg{width:14px;height:14px;fill:var(--lime)}

  .band{position:absolute;left:0;bottom:0;width:600px;height:40px}
  .website{position:absolute;right:34px;bottom:12px;color:#fff;font-weight:700;font-style:italic;font-size:13px;letter-spacing:0.3px}
</style>
</head>
<body>

<section class="card card--front" aria-label="Card front">
  <div class="wordmark">Kelvor Engineers</div>
  <div class="tagline">MULTI-DISCIPLINE ENGINEERING</div>
  <div class="locations">Ridgeport | Calder Bay | Mesa Norte | Fenwick</div>
</section>

<section class="card card--back" aria-label="Card back">
  <div class="wordmark">Kelvor Engineers</div>
  <div class="person">DANA HALLOWAY REYES</div>
  <div class="rule"></div>
  <ul class="contacts">
    <li><svg viewBox="0 0 24 24"><path d="M6.6 10.8a15.1 15.1 0 0 0 6.6 6.6l2.2-2.2c.3-.3.7-.4 1-.2 1.1.4 2.3.6 3.6.6.6 0 1 .4 1 1V20c0 .6-.4 1-1 1A17 17 0 0 1 3 4c0-.6.4-1 1-1h3.5c.6 0 1 .4 1 1 0 1.3.2 2.5.6 3.6.1.3 0 .7-.2 1z"/></svg>555.014.2290</li>
    <li><svg viewBox="0 0 24 24"><path d="M7 1h10a2 2 0 0 1 2 2v18a2 2 0 0 1-2 2H7a2 2 0 0 1-2-2V3a2 2 0 0 1 2-2zm0 3v14h10V4zm5 15.5a1.2 1.2 0 1 0 0 2.4 1.2 1.2 0 0 0 0-2.4z"/></svg>555.017.3841</li>
    <li><svg viewBox="0 0 24 24"><path d="M2 5h20v14H2zm2 2v.5l8 5 8-5V7zm0 2.8V17h16V9.8l-8 5z"/></svg>dreyes@kelvorstruct.com</li>
  </ul>
  <svg class="band" viewBox="0 0 600 40" preserveAspectRatio="none" aria-hidden="true">
    <path d="M0 10H410q6 0 8-4l2-3q2-3 7-3H600V40H0z" fill="var(--navy)"/>
    <path d="M0 10H412q4 0 6-4l1-2V12q-2 9-10 9H0z" fill="var(--lime)"/>
    <path d="M0 16H408q8 0 10-8" fill="none" stroke="#fff" stroke-width="1.5"/>
  </svg>
  <div class="website">www.kelvorstruct.com</div>
</section>

</body>
</html>
```